Business Card Design

Please copy the format of the attached card.

FRONT:
White text small blue horses head logo where "mivar" in in example

BACK:
Blue background w/ white horses head

Industry/Entity Type

Business

Contact Information for Business Card

Colby Marsh
Chief Executive Officer
Tundrel Inns & Resorts
417 Fenwick Street | San Francisco, California 94327
Tel: +1.415.772.3841
email: colby@tundrelinns.com

```html
<!DOCTYPE html>
<html lang="en">
<head>
<meta charset="utf-8">
<title>mivar business card</title>
<link rel="stylesheet" href="https://fonts.googleapis.com/css2?family=Open+Sans:wght@300;400;600&display=swap">
<style>
  :root {
    --navy: #1b4587;
    --navy-deep: #15386f;
    --paper: #fbfbfb;
    --ink: #555a60;
    --rule: #b9bcc0;
    --backdrop: #e9e7e3;
  }
  * { margin: 0; padding: 0; box-sizing: border-box; }
  html, body { width: 1200px; height: 1023px; overflow: hidden; }
  body {
    background: var(--backdrop);
    font-family: "Open Sans", Arial, sans-serif;
    position: relative;
  }
  .card {
    position: absolute;
    left: 320px;
    width: 560px;
    height: 320px;
    border-radius: 3px;
    overflow: hidden;
    box-shadow: 0 6px 18px rgba(0,0,0,0.18);
  }
  .card-front { top: 161px; background: var(--paper); }
  .card-back { top: 541px; background: var(--navy); }

  .front-wave { position: absolute; left: 0; bottom: 0; width: 560px; height: 120px; }

  .brand { position: absolute; display: flex; align-items: center; gap: 12px; }
  .brand-mark { width: 30px; height: 30px; border-radius: 50%; }
  .brand-name { font-weight: 300; letter-spacing: 1px; line-height: 1; }

  .card-front .brand { right: 56px; top: 52px; }
  .card-front .brand-mark { background: var(--navy); }
  .card-front .brand-name { color: var(--ink); font-size: 40px; }

  .person { position: absolute; left: 38px; top: 168px; }
  .person-name { color: var(--navy); font-weight: 600; font-size: 16px; line-height: 1.2; }
  .person-title { color: var(--ink); font-weight: 300; font-size: 15px; line-height: 1.3; }

  .contact { position: absolute; left: 38px; top: 228px; list-style: none; }
  .contact li {
    display: flex; align-items: center; gap: 7px;
    color: var(--ink); font-weight: 300; font-size: 12.5px; line-height: 1.6;
  }
  .contact svg { width: 12px; height: 12px; fill: var(--navy); }

  .address {
    position: absolute; left: 292px; top: 178px;
    color: var(--ink); font-weight: 300; font-size: 13px; line-height: 1.45;
    font-style: normal;
  }

  .card-back .brand { left: 50%; top: 50%; transform: translate(-50%, -50%); }
  .card-back .brand-mark { background: #ffffff; width: 44px; height: 44px; }
  .card-back .brand-name { color: #ffffff; font-size: 52px; }
</style>
</head>
<body>

<section class="card card-front">
  <svg class="front-wave" viewBox="0 0 560 120" preserveAspectRatio="none" aria-hidden="true">
    <path d="M0 112 C150 104 260 80 380 46 C450 26 510 10 560 4 L560 120 L0 120 Z" fill="var(--rule)"/>
    <path d="M0 116 C150 110 260 88 380 54 C450 34 510 18 560 12 L560 120 L0 120 Z" fill="var(--navy)"/>
  </svg>

  <div class="brand">
    <span class="brand-mark"></span>
    <span class="brand-name">mivar</span>
  </div>

  <div class="person">
    <p class="person-name">Colby Marsh</p>
    <p class="person-title">Chief Executive Officer</p>
  </div>

  <ul class="contact">
    <li>
      <svg viewBox="0 0 24 24" aria-hidden="true"><path d="M6.6 10.8a15.1 15.1 0 0 0 6.6 6.6l2.2-2.2a1 1 0 0 1 1-.25 11.4 11.4 0 0 0 3.6.57 1 1 0 0 1 1 1V20a1 1 0 0 1-1 1A17 17 0 0 1 3 4a1 1 0 0 1 1-1h3.5a1 1 0 0 1 1 1c0 1.25.2 2.45.57 3.57a1 1 0 0 1-.25 1z"/></svg>
      +1.415.772.3841
    </li>
    <li>
      <svg viewBox="0 0 24 24" aria-hidden="true"><path d="M2 5h20v14H2z M2 5l10 8 10-8" fill="none" stroke="var(--navy)" stroke-width="2.4"/></svg>
      colby@tundrelinns.com
    </li>
  </ul>

  <address class="address">
    417 Fenwick Street, San Francisco<br>
    California, 94327
  </address>
</section>

<section class="card card-back">
  <div class="brand">
    <span class="brand-mark"></span>
    <span class="brand-name">mivar</span>
  </div>
</section>

</body>
</html>
```